Business Card For Halvenmoor Financial Consulting

Hi, I would like a business card designed. Bold, modern.
Please use the same design as the logo. I have also attached the website design to see the overall theme.
Wordmark Font
Color: Hex: #01AEF7

```html
<!DOCTYPE html>
<html lang="en">
<head>
<meta charset="utf-8">
<title>Halvenmoor Financial Consulting – Business Card</title>
<link rel="stylesheet" href="https://fonts.googleapis.com/css2?family=Montserrat:wght@400;500;700&display=swap">
<style>
  :root {
    --stage: #3b3b3b;
    --card: #17222d;
    --card-deep: #111a23;
    --accent: #01aef7;
    --ink: #ffffff;
    --muted: #c9d3dc;
  }
  * { box-sizing: border-box; margin: 0; padding: 0; }
  html, body { width: 1200px; height: 801px; overflow: hidden; }
  body {
    background: var(--stage);
    font-family: "Montserrat", Arial, sans-serif;
    color: var(--ink);
    position: relative;
  }
  .card {
    position: absolute;
    top: 246px;
    width: 540px;
    height: 309px;
    background: var(--card);
    border-bottom: 4px solid var(--accent);
    overflow: hidden;
  }
  .card--front { left: 40px; }
  .card--back { left: 620px; }

  /* Front */
  .brand {
    position: absolute;
    left: 42px;
    top: 54px;
    display: flex;
    align-items: center;
    gap: 14px;
  }
  .brand__mark {
    width: 46px;
    height: 46px;
    border: 4px solid var(--accent);
    flex: none;
  }
  .brand__name {
    font-weight: 700;
    font-size: 21px;
    line-height: 1.15;
    letter-spacing: 1px;
    text-transform: uppercase;
    color: var(--ink);
  }
  .person {
    position: absolute;
    left: 42px;
    top: 150px;
  }
  .person__name {
    font-weight: 700;
    font-size: 19px;
    letter-spacing: 0.5px;
    text-transform: uppercase;
    color: var(--accent);
  }
  .person__role {
    font-size: 13px;
    color: var(--muted);
    margin-top: 4px;
  }
  .divider {
    position: absolute;
    left: 290px;
    top: 140px;
    width: 1px;
    height: 66px;
    background: var(--accent);
  }
  .contact {
    position: absolute;
    left: 308px;
    top: 138px;
    list-style: none;
    font-size: 13px;
    color: var(--muted);
  }
  .contact li {
    display: flex;
    align-items: center;
    gap: 8px;
    height: 23px;
  }
  .contact svg { width: 12px; height: 12px; fill: var(--accent); flex: none; }
  .address {
    position: absolute;
    left: 42px;
    bottom: 34px;
    font-size: 13px;
    color: var(--muted);
  }

  /* Back */
  .pattern-field {
    position: absolute;
    inset: 0;
    background: linear-gradient(135deg, #24313e 0%, var(--card) 45%, var(--card-deep) 100%);
  }
  .back-brand {
    position: absolute;
    left: 50%;
    top: 50%;
    transform: translate(-50%, -50%);
    display: flex;
    align-items: center;
    gap: 14px;
  }
  .back-brand .brand__name { font-size: 23px; }
</style>
</head>
<body>
  <article class="card card--front" aria-label="Card front">
    <div class="brand">
      <span class="brand__mark"></span>
      <span class="brand__name">Halvenmoor<br>Financial Consulting</span>
    </div>

    <div class="person">
      <p class="person__name">Marcus Tellwin</p>
      <p class="person__role">President</p>
    </div>

    <span class="divider"></span>

    <ul class="contact">
      <li>
        <svg viewBox="0 0 24 24" aria-hidden="true"><path d="M6.6 10.8a15.1 15.1 0 0 0 6.6 6.6l2.2-2.2a1 1 0 0 1 1-.25 11.4 11.4 0 0 0 3.6.57 1 1 0 0 1 1 1V20a1 1 0 0 1-1 1A17 17 0 0 1 3 4a1 1 0 0 1 1-1h3.5a1 1 0 0 1 1 1c0 1.25.2 2.45.57 3.57a1 1 0 0 1-.25 1z"/></svg>
        555-014-2287
      </li>
      <li>
        <svg viewBox="0 0 24 24" aria-hidden="true"><path d="M2 5h20v14H2zm2 2v.5l8 5 8-5V7z"/></svg>
        marcus@halvenmoor.com
      </li>
      <li>
        <svg viewBox="0 0 24 24" aria-hidden="true"><circle cx="12" cy="12" r="10"/></svg>
        www.halvenmoor.com
      </li>
    </ul>

    <p class="address">1180 Harbor Crest Way, Bayview CA 90210</p>
  </article>

  <article class="card card--back" aria-label="Card back">
    <div class="pattern-field" role="img" aria-label="Embossed repeating tile pattern in dark navy tones"></div>
    <div class="back-brand">
      <span class="brand__mark"></span>
      <span class="brand__name">Halvenmoor<br>Financial Consulting</span>
    </div>
  </article>
</body>
</html>
```